Brookmere Osteopathy flyer

I want a clean clear DL flyer (but also want an A4 poster) promoting a new Osteopathic business in a semi rural area in Tasmania (Australia).
It can have pictures like the examples attached to show people what Osteopathy is (its like Chiropractic and physiotherapy).
I am the sole practioner and am male, so any pictures would be best to be a white male if possible.
I've attached some wording, you can use all, or none of it
I don't have a phone number for the business yet
info@brookmereosteopathy.example
www.brookmereosteopathy.example
Target Market(s)
Australians, from tradies, professionals, babies to retired people
Industry/Entity Type
Health
Look and feel

```html
<!DOCTYPE html>
<html lang="en">
<head>
<meta charset="utf-8">
<title>Brookmere Osteopathy Flyer</title>
<link href="https://fonts.googleapis.com/css2?family=Montserrat:wght@300;400;500;600;700;800&family=Source+Sans+3:wght@600&display=swap" rel="stylesheet">
<style>
  :root {
    --backdrop: #444444;
    --blue: #1e96d2;
    --orange: #ef9746;
    --white: #ffffff;
    --photo-light: #c9d4dc;
    --photo-skin: #c99a78;
    --photo-deep: #5f7f95;
  }
  * { margin: 0; padding: 0; box-sizing: border-box; }
  html, body { width: 897px; height: 1200px; overflow: hidden; background: var(--backdrop); }
  .flyer {
    position: absolute; left: 103px; top: 112px;
    width: 691px; height: 975px;
    background: var(--blue); overflow: hidden;
    font-family: "Montserrat", sans-serif; color: var(--white);
  }
  .hero-photo {
    position: absolute; left: 0; top: 0; width: 691px; height: 500px;
    background: linear-gradient(120deg, var(--photo-light) 0%, var(--photo-skin) 45%, #7a6150 75%, var(--photo-deep) 100%);
  }
  .shapes { position: absolute; left: 0; top: 0; }
  .logo-tab {
    position: absolute; left: 256px; top: 0; width: 178px; height: 205px;
    background: var(--white); border-radius: 0 0 89px 89px;
    display: flex; align-items: center; justify-content: center; gap: 6px;
    padding-top: 20px;
  }
  .logo-tab .mark { width: 10px; height: 10px; border-radius: 50%; background: var(--blue); flex: none; }
  .logo-tab .name {
    font-size: 15px; font-weight: 600; color: var(--blue); line-height: 1.25; text-align: center;
  }
  .service-photo {
    position: absolute; border-radius: 50%; border: 4px solid var(--orange);
  }
  .service-photo.abdomen { left: 75px; top: 298px; width: 186px; height: 186px;
    background: linear-gradient(150deg, #eeeeee, #c8a286 60%, #e8e8e8); }
  .service-photo.shoulder { left: 231px; top: 249px; width: 228px; height: 228px;
    background: linear-gradient(160deg, #e6e6e6, #d1b29c 50%, #cfdbe8 85%); }
  .service-photo.infant { left: 432px; top: 298px; width: 186px; height: 186px;
    background: linear-gradient(170deg, #d7d8e0, #e8c8b6 45%, #5aaad6 75%, #cfd6e0); }
  .title { position: absolute; left: 0; width: 691px; text-align: center; line-height: 1; }
  .title.light { top: 500px; font-size: 60px; font-weight: 300; letter-spacing: 1px; }
  .title.bold { top: 553px; font-size: 57px; font-weight: 800; letter-spacing: -0.5px; }
  .reasons-tag {
    position: absolute; left: 166px; top: 618px; width: 358px; height: 56px;
    background: var(--orange); border-radius: 16px 0 16px 0;
    text-align: center; font-size: 22px; font-weight: 700; line-height: 1.1;
    padding-top: 4px; letter-spacing: -0.4px;
  }
  .reasons { position: absolute; top: 704px; list-style: none;
    font-family: "Source Sans 3", sans-serif; font-weight: 600; font-size: 15.5px; }
  .reasons.left { left: 78px; }
  .reasons.right { left: 339px; }
  .reasons li { height: 21px; display: flex; align-items: center; gap: 7px; }
  .reasons svg { width: 14px; height: 14px; flex: none; }
  .summary {
    position: absolute; left: 0; top: 826px; width: 691px; text-align: center;
    font-family: "Source Sans 3", sans-serif; font-weight: 600; font-size: 12.6px; line-height: 1.12;
  }
  .contact { position: absolute; left: 42px; top: 904px; list-style: none; font-size: 13.5px; font-weight: 500; }
  .contact li { height: 19.3px; display: flex; align-items: center; gap: 8px; }
  .contact svg { width: 13px; height: 13px; flex: none; }
  .call-blob { position: absolute; left: 0; top: 0; }
  .call { position: absolute; right: 33px; text-align: right; font-weight: 800; }
  .call.label { top: 900px; font-size: 17px; letter-spacing: -0.3px; }
  .call.number { top: 917px; font-size: 30px; letter-spacing: 1px; }
</style>
</head>
<body>
<main class="flyer">
  <div class="hero-photo" role="img" aria-label="Practitioner's hands treating a woman's upper back and shoulder"></div>

  <svg class="shapes" width="691" height="975" viewBox="0 0 691 975" aria-hidden="true">
    <path d="M0,438 C200,360 480,330 691,373 L691,450 C480,420 200,430 0,492 Z" fill="var(--white)"/>
    <path d="M0,492 C200,430 480,420 691,450 L691,510 L0,510 Z" fill="var(--blue)"/>
  </svg>

  <div class="logo-tab">
    <span class="mark"></span>
    <span class="name">Brookmere<br>Osteopathy</span>
  </div>

  <div class="service-photo abdomen" role="img" aria-label="Osteopath treating a patient's abdomen"></div>
  <div class="service-photo infant" role="img" aria-label="Gentle cranial treatment of a sleeping baby"></div>
  <div class="service-photo shoulder" role="img" aria-label="Woman lying on a treatment table having her arm and shoulder stretched"></div>

  <h1 class="title light">BROOKMERE</h1>
  <h2 class="title bold">OSTEOPATHY</h2>

  <div class="reasons-tag">Common Reasons<br>People Visit An Osteopath:</div>

  <ul class="reasons left">
    <li><svg viewBox="0 0 14 14"><circle cx="7" cy="7" r="5.8" fill="none" stroke="#fff" stroke-width="1.6"/><path d="M4.2,7 L6.4,9.2 L12.8,2.5" fill="none" stroke="#fff" stroke-width="1.8" stroke-linecap="round"/></svg>Back / neck pain</li>
    <li><svg viewBox="0 0 14 14"><circle cx="7" cy="7" r="5.8" fill="none" stroke="#fff" stroke-width="1.6"/><path d="M4.2,7 L6.4,9.2 L12.8,2.5" fill="none" stroke="#fff" stroke-width="1.8" stroke-linecap="round"/></svg>Headaches / migraines</li>
    <li><svg viewBox="0 0 14 14"><circle cx="7" cy="7" r="5.8" fill="none" stroke="#fff" stroke-width="1.6"/><path d="M4.2,7 L6.4,9.2 L12.8,2.5" fill="none" stroke="#fff" stroke-width="1.8" stroke-linecap="round"/></svg>Joint and muscle pain</li>
    <li><svg viewBox="0 0 14 14"><circle cx="7" cy="7" r="5.8" fill="none" stroke="#fff" stroke-width="1.6"/><path d="M4.2,7 L6.4,9.2 L12.8,2.5" fill="none" stroke="#fff" stroke-width="1.8" stroke-linecap="round"/></svg>Pregnancy-related discomfort</li>
    <li><svg viewBox="0 0 14 14"><circle cx="7" cy="7" r="5.8" fill="none" stroke="#fff" stroke-width="1.6"/><path d="M4.2,7 L6.4,9.2 L12.8,2.5" fill="none" stroke="#fff" stroke-width="1.8" stroke-linecap="round"/></svg>Disc related issues</li>
  </ul>
  <ul class="reasons right">
    <li><svg viewBox="0 0 14 14"><circle cx="7" cy="7" r="5.8" fill="none" stroke="#fff" stroke-width="1.6"/><path d="M4.2,7 L6.4,9.2 L12.8,2.5" fill="none" stroke="#fff" stroke-width="1.8" stroke-linecap="round"/></svg>Sciatica</li>
    <li><svg viewBox="0 0 14 14"><circle cx="7" cy="7" r="5.8" fill="none" stroke="#fff" stroke-width="1.6"/><path d="M4.2,7 L6.4,9.2 L12.8,2.5" fill="none" stroke="#fff" stroke-width="1.8" stroke-linecap="round"/></svg>Plantar fasciitis</li>
    <li><svg viewBox="0 0 14 14"><circle cx="7" cy="7" r="5.8" fill="none" stroke="#fff" stroke-width="1.6"/><path d="M4.2,7 L6.4,9.2 L12.8,2.5" fill="none" stroke="#fff" stroke-width="1.8" stroke-linecap="round"/></svg>Tendonitis / Bursitis</li>
    <li><svg viewBox="0 0 14 14"><circle cx="7" cy="7" r="5.8" fill="none" stroke="#fff" stroke-width="1.6"/><path d="M4.2,7 L6.4,9.2 L12.8,2.5" fill="none" stroke="#fff" stroke-width="1.8" stroke-linecap="round"/></svg>Adhesive capsulitis (frozen shoulder)</li>
    <li><svg viewBox="0 0 14 14"><circle cx="7" cy="7" r="5.8" fill="none" stroke="#fff" stroke-width="1.6"/><path d="M4.2,7 L6.4,9.2 L12.8,2.5" fill="none" stroke="#fff" stroke-width="1.8" stroke-linecap="round"/></svg>Tennis / Golfers elbow</li>
  </ul>

  <p class="summary">Osteopaths use a combination of joint manipulation, targeted deep tissue massage and stretching<br>to improve function, relieve pain and support the body’s ability to heal itself.</p>

  <svg class="call-blob" width="691" height="975" viewBox="0 0 691 975" aria-hidden="true">
    <path d="M393,975 C393,905 470,862 590,860 C635,859 668,866 691,874 L691,975 Z" fill="var(--orange)"/>
  </svg>

  <ul class="contact">
    <li><svg viewBox="0 0 14 14"><path d="M7,13 C7,13 2.5,8.2 2.5,5.2 A4.5,4.5 0 0 1 11.5,5.2 C11.5,8.2 7,13 7,13 Z" fill="none" stroke="#fff" stroke-width="1.1"/><circle cx="7" cy="5.2" r="1.6" fill="none" stroke="#fff" stroke-width="1.1"/></svg>48 Ridgeline Road, Brookmere</li>
    <li><svg viewBox="0 0 14 14"><circle cx="7" cy="7" r="5.8" fill="none" stroke="#fff" stroke-width="1.1"/><ellipse cx="7" cy="7" rx="2.6" ry="5.8" fill="none" stroke="#fff" stroke-width="1.1"/><path d="M1.2,7 H12.8 M2,4 H12 M2,10 H12" stroke="#fff" stroke-width="1"/></svg>www.brookmereosteopathy.example</li>
    <li><svg viewBox="0 0 14 14"><rect x="1" y="3" width="12" height="8.5" rx="1" fill="none" stroke="#fff" stroke-width="1.1"/><path d="M1.3,3.5 L7,8 L12.7,3.5" fill="none" stroke="#fff" stroke-width="1.1"/></svg>info@brookmereosteopathy.example</li>
  </ul>

  <p class="call label">CALL US NOW!</p>
  <p class="call number">03 5550 1842</p>
</main>
</body>
</html>
```